New Bicycle shop business card

Hi!
I'm looking for a business card for my new proffesional bike mechanics shop. This shop is only for fixing broken bikes and not selling bikes.
Peferbly a modern and sleek and modern design.
Colors: black, grey, red, white
Information:
Name: Rijwielwerkplaats Vanhoutte
Shop owner: Bart Vanhoutte & Marieke Segers
Website: www.rijwielwerkplaats-vanhoutte.be
Email: info@rijwielwerkplaats-vanhoutte.be
Phone number: +32471902368
Street adres: Kerkweg 46
9940 Bellebeke
Slogan/shop information: Herstellingen van alle merken.
Logo: see files.
Target Market(s)
People who seek a mechanic to fix or upgrade their bikes.
Contact Information for Business Card
Information:
Website: info@rijwielwerkplaats-vanhoutte.be
9940 Bellebeke
Logo: see files.

```html
<!DOCTYPE html>
<html lang="nl">
<head>
<meta charset="utf-8">
<title>Rijwielwerkplaats Vanhoutte – visitekaartje</title>
<link rel="stylesheet" href="https://fonts.googleapis.com/css2?family=Montserrat:wght@700&family=Questrial&display=swap">
<style>
  :root {
    --backdrop: #d9d6d1;
    --card-black: #050505;
    --band-dark: #141414;
    --band-light: #1d1d1d;
    --accent-red: #e21f3d;
    --text-white: #ffffff;
    --text-grey: #b9b9b9;
  }
  * { box-sizing: border-box; margin: 0; padding: 0; }
  html, body { width: 1189px; height: 1200px; overflow: hidden; }
  body { background: var(--backdrop); position: relative; font-family: "Questrial", sans-serif; }

  .card {
    position: absolute; left: 169px; width: 851px; height: 485px;
    background: var(--card-black); border-radius: 30px; overflow: hidden;
    box-shadow: 0 6px 18px rgba(0,0,0,.35);
  }
  .card--front { top: 112px; }
  .card--back { top: 641px; }

  .band {
    position: absolute; left: 0; right: 0;
    background: radial-gradient(ellipse at center, var(--band-light), var(--band-dark) 75%);
  }
  .rule { position: absolute; left: 0; right: 0; height: 5px; background: var(--accent-red); }

  .card--front .band { top: 118px; height: 252px; }
  .card--front .rule--top { top: 113px; }
  .card--front .rule--bottom { top: 368px; }

  .front-name {
    position: absolute; left: 0; right: 0; top: 160px; text-align: center;
    font-family: "Montserrat", sans-serif; font-weight: 700; color: var(--text-white);
    font-size: 44px; line-height: 1.08; letter-spacing: 2px;
  }
  .front-name span { display: block; letter-spacing: 14px; font-size: 34px; }
  .tagline {
    position: absolute; left: 0; right: 0; top: 284px; text-align: center;
    color: var(--text-white); font-size: 23px; letter-spacing: 4px;
  }

  .card--back .band { top: 57px; height: 373px; }
  .card--back .rule--top { top: 52px; }
  .card--back .rule--bottom { top: 428px; }

  .back-name {
    position: absolute; left: 68px; top: 104px;
    font-family: "Montserrat", sans-serif; font-weight: 700; color: var(--text-white);
    font-size: 28px; line-height: 1.1; letter-spacing: 1px;
  }
  .back-name span { display: block; font-size: 24px; letter-spacing: 9px; }
  .owners {
    position: absolute; left: 68px; top: 222px;
    color: var(--text-white); font-size: 21px; letter-spacing: .3px;
  }
  .contact-list { position: absolute; left: 68px; top: 274px; list-style: none; }
  .contact-list li {
    display: flex; align-items: center; height: 30.5px;
    color: var(--text-white); font-size: 19px;
  }
  .contact-list svg { width: 25px; height: 25px; margin-right: 16px; flex: none; }

  .brand-spot { position: absolute; left: 540px; top: 140px; width: 190px; text-align: center; }
  .brand-spot__disc {
    width: 150px; height: 150px; margin: 0 auto 18px; border-radius: 50%;
    background: var(--accent-red);
  }
  .brand-spot__name {
    font-family: "Montserrat", sans-serif; font-weight: 700; color: var(--text-white);
    font-size: 14px; letter-spacing: 1px; line-height: 1.3;
  }
</style>
</head>
<body>

<section class="card card--front">
  <div class="rule rule--top"></div>
  <div class="band"></div>
  <div class="rule rule--bottom"></div>
  <h1 class="front-name">RIJWIELWERKPLAATS<span>VANHOUTTE</span></h1>
  <p class="tagline">Herstellingen van alle merken</p>
</section>

<section class="card card--back">
  <div class="rule rule--top"></div>
  <div class="band"></div>
  <div class="rule rule--bottom"></div>

  <h2 class="back-name">RIJWIELWERKPLAATS<span>VANHOUTTE</span></h2>
  <p class="owners">BART VANHOUTTE &amp; MARIEKE SEGERS</p>

  <ul class="contact-list">
    <li>
      <svg viewBox="0 0 24 24" aria-hidden="true"><circle cx="12" cy="12" r="11" fill="#e21f3d"/><path d="M8.6 6.5l1.8 2.4-1.1 1.4c.7 1.6 1.9 2.8 3.5 3.6l1.4-1.1 2.4 1.8-1 2c-4.5-.3-8.1-3.9-8.3-8.4z" fill="#fff"/></svg>
      +32471902368
    </li>
    <li>
      <svg viewBox="0 0 24 24" aria-hidden="true"><circle cx="12" cy="12" r="11" fill="#e21f3d"/><rect x="6.5" y="8" width="11" height="8" rx="1" fill="#fff"/><path d="M6.8 8.4l5.2 4 5.2-4" stroke="#e21f3d" stroke-width="1.2" fill="none"/></svg>
      info@rijwielwerkplaats-vanhoutte.be
    </li>
    <li>
      <svg viewBox="0 0 24 24" aria-hidden="true"><circle cx="12" cy="12" r="11" fill="#e21f3d"/><g stroke="#fff" stroke-width="1.1" fill="none"><circle cx="12" cy="12" r="5.5"/><ellipse cx="12" cy="12" rx="2.4" ry="5.5"/><path d="M6.5 12h11M7.3 9.2h9.4M7.3 14.8h9.4"/></g></svg>
      www.rijwielwerkplaats-vanhoutte.be
    </li>
    <li>
      <svg viewBox="0 0 24 24" aria-hidden="true"><circle cx="12" cy="12" r="11" fill="#e21f3d"/><path d="M12 18s-4.5-4.7-4.5-8a4.5 4.5 0 0 1 9 0c0 3.3-4.5 8-4.5 8z" fill="#fff"/><circle cx="12" cy="10" r="1.7" fill="#e21f3d"/></svg>
      Kerkweg 46, 9940 Bellebeke
    </li>
  </ul>

  <div class="brand-spot">
    <div class="brand-spot__disc"></div>
    <p class="brand-spot__name">RIJWIELWERKPLAATS VANHOUTTE</p>
  </div>
</section>

</body>
</html>
```